Business card for law firm

Need business card for new law firm. Think confident, authoritative, conservative, but not stuffy or old-fashioned.

Contact Information for Business Card

Content for card - logo (uploaded), plus the following:

Paul Whitcombe (larger font)
Managing Partner (larger font, but not as large as name)
Level 9, 7 Ferris Lane
Sydney NSW 2000
Main Tel 02 9364 2710
Direct Tel 02 8472 3159
Email paul@qvlegal.com.au
www.qvlegal.com.au

Letterhead design should include logo plus:
Level 9, 7 Ferris Lane
Sydney NSW 2000
Tel 02 8472 3159
www.qvlegal.com.au

```html
<!DOCTYPE html>
<html lang="en">
<head>
<meta charset="utf-8">
<title>Quayview Legal — Letterhead</title>
<link href="https://fonts.googleapis.com/css2?family=Questrial&family=Roboto:wght@400&display=swap" rel="stylesheet">
<style>
  :root{
    --backdrop:#e4e5e7;
    --paper:#f1f1f2;
    --paper-edge:#dcdcde;
    --navy:#1e2f63;
    --body-text:#7a7a7c;
    --salutation:#808082;
    --rule:#3a4f86;
    --signature-fill:#c9d3ea;
  }
  *{box-sizing:border-box;margin:0;padding:0}
  html,body{width:1024px;height:1200px;overflow:hidden}
  body{background:var(--backdrop);font-family:"Questrial",sans-serif}
  .letterhead{
    position:absolute;left:88px;top:0;width:848px;height:1200px;
    background:linear-gradient(135deg,#f6f6f7 0%,var(--paper) 45%,#e8e8ea 100%);
    border-left:1px solid var(--paper-edge);border-right:1px solid var(--paper-edge);
  }
  .brand{
    position:absolute;top:70px;left:0;width:100%;
    display:flex;flex-direction:column;align-items:center;gap:14px;
  }
  .brand-square{width:34px;height:34px;background:var(--navy)}
  .brand-name{
    font-family:"Questrial",sans-serif;color:var(--navy);
    font-size:26px;letter-spacing:3px;text-transform:uppercase;
  }
  .letter{
    position:absolute;left:80px;top:318px;width:698px;color:var(--body-text);
  }
  .salutation{font-size:21px;color:var(--salutation);margin-bottom:34px}
  .letter-body p{font-size:12.6px;line-height:14.6px;text-align:justify;margin-bottom:15px}
  .closing{font-size:12.6px;margin-top:34px}
  .signature{
    display:block;margin-top:48px;width:150px;height:62px;
    background:linear-gradient(100deg,var(--signature-fill),rgba(201,211,234,.35));
    border-radius:4px;
  }
  .footer{
    position:absolute;left:0;top:1071px;width:100%;
    display:flex;flex-direction:column;align-items:center;
  }
  .footer-rule{
    position:relative;width:570px;height:28px;display:flex;justify-content:center;align-items:center;
  }
  .footer-rule::before{
    content:"";position:absolute;left:0;right:0;top:50%;height:1px;
    background:linear-gradient(90deg,transparent,var(--rule) 25%,var(--rule) 75%,transparent);
  }
  .contact-icons{position:relative;display:flex;gap:4px}
  .contact-icons svg{display:block}
  .footer-address{
    font-family:"Roboto",sans-serif;color:var(--navy);font-size:15px;line-height:20px;
    text-align:center;margin-top:8px;
  }
</style>
</head>
<body>
<main class="letterhead">
  <header class="brand">
    <span class="brand-square"></span>
    <span class="brand-name">Quayview Legal</span>
  </header>

  <section class="letter">
    <p class="salutation">Dear Mr. Carter,</p>
    <div class="letter-body">
      <p>Lorem ipsum dolor sit amet, consectetur adipiscing elit. Donec orci purus, luctus vitae dignissim eu, iaculis sed purus. Vivamus faucibus, ipsum nec aliquet viverra, leo mauris condimentum ligula, sit amet sagittis enim ligula quis arcu. Nam egestas tortor id nisi porttitor mattis. In tortor ante, ultricies in suscipit a, tempus non massa. Vivamus et auctor mi. Fusce vel massa nulla. Phasellus nec eros mauris, et scelerisque orci.</p>
      <p>Donec malesuada orci vitae nulla accumsan porta a id massa. Quisque accumsan iaculis magna sit amet fringilla. Maecenas consequat, magna eget tincidunt semper, odio nibh rutrum mi, id feugiat ante nisi eu risus. Vestibulum nunc orci, rhoncus a placerat in, ultricies in mi. Cras mattis varius eros, vel fringilla nisi suscipit eget. Quisque scelerisque sagittis nulla at porttitor.</p>
      <p>Sed id augue vitae urna euismod commodo aliquet a quam. Pellentesque arcu velit, cursus et malesuada ut, consequat et diam. Nullam erat sem, rhoncus id ullamcorper vitae, rhoncus et arcu. In ultricies ultricies nulla, ut rutrum nisi iaculis at. Donec eu magna a metus ornare faucibus. Fusce aliquet faucibus ultricies. Morbi semper, est id tincidunt gravida, sem arcu adipiscing lacus, ac bibendum nulla leo eu purus. Quisque nec diam sed risus consectetur accumsan quis quis nibh. Vestibulum id purus lorem.</p>
      <p>It is a long established fact that a reader will be distracted by the readable content of a page when looking at its layout. The point of using Lorem Ipsum is that it has a more-or-less normal distribution of letters, as opposed to using 'Content here, content here', making it look like readable English. Many desktop publishing packages</p>
    </div>
    <p class="closing">Sincerely,</p>
    <span class="signature" role="img" aria-label="Handwritten signature of Daniel Hale"></span>
  </section>

  <footer class="footer">
    <div class="footer-rule">
      <div class="contact-icons">
        <svg width="26" height="26" viewBox="0 0 26 26" aria-label="Address">
          <circle cx="13" cy="13" r="13" fill="var(--navy)"/>
          <path d="M13 6.5a4.3 4.3 0 0 0-4.3 4.3c0 3.2 4.3 8.2 4.3 8.2s4.3-5 4.3-8.2A4.3 4.3 0 0 0 13 6.5z" fill="#fff"/>
          <circle cx="13" cy="10.8" r="1.6" fill="var(--navy)"/>
        </svg>
        <svg width="26" height="26" viewBox="0 0 26 26" aria-label="Phone">
          <circle cx="13" cy="13" r="13" fill="var(--navy)"/>
          <path d="M9.3 7.2l1.9-.4 1.2 2.9-1.3 1.1a8 8 0 0 0 3.9 3.9l1.1-1.3 2.9 1.2-.4 1.9c-.2.7-.8 1.1-1.5 1.1-4.6-.3-8.6-4.3-8.9-8.9 0-.7.4-1.3 1.1-1.5z" fill="#fff"/>
        </svg>
        <svg width="26" height="26" viewBox="0 0 26 26" aria-label="Website">
          <circle cx="13" cy="13" r="13" fill="var(--navy)"/>
          <circle cx="13" cy="13" r="6" fill="none" stroke="#fff" stroke-width="1.4"/>
          <ellipse cx="13" cy="13" rx="2.6" ry="6" fill="none" stroke="#fff" stroke-width="1.2"/>
          <path d="M7 13h12" stroke="#fff" stroke-width="1.2"/>
        </svg>
      </div>
    </div>
    <address class="footer-address" style="font-style:normal">
      Level 9, 7 Ferris Lane, Sydney NSW 2000<br>
      02 8472 3159 | www.qvlegal.com.au
    </address>
  </footer>
</main>
</body>
</html>
```